TA BRAMLEY BUSINESS CARD DESIGN PROJECT

We need to utilize our logo that was expertly created on PixelHarbor and now need to match this with a business card design.

```html
<!DOCTYPE html>
<html lang="en">
<head>
<meta charset="utf-8">
<title>TA BRAMLEY Business Card</title>
<link href="https://fonts.googleapis.com/css2?family=Montserrat:wght@400;500;700;800&display=swap" rel="stylesheet">
<style>
  :root {
    --backdrop: #1e1e1e;
    --card-black: #161616;
    --brand-blue: #1058b0;
    --ink-white: #ffffff;
    --rule-dark: #0f0f0f;
  }
  * { margin: 0; padding: 0; box-sizing: border-box; }
  html, body {
    width: 1200px; height: 900px; overflow: hidden;
    background: var(--backdrop);
    font-family: "Montserrat", sans-serif;
  }
  .canvas { position: relative; width: 1200px; height: 900px; }

  .card {
    position: absolute;
    width: 525px; height: 300px;
    border-radius: 18px;
    overflow: hidden;
    box-shadow: 0 18px 40px rgba(0,0,0,0.55);
  }

  /* Front */
  .card-front { left: 70px; top: 470px; background: var(--card-black); }
  .front-wave { position: absolute; left: 0; top: 0; width: 525px; height: 300px; }
  .front-brand {
    position: absolute; left: 30px; top: 102px; width: 210px;
    color: var(--brand-blue); font-weight: 800; font-size: 26px;
    line-height: 32px; letter-spacing: 3px; text-align: center;
  }
  .front-divider {
    position: absolute; left: 262px; top: 48px; width: 2px; height: 160px;
    background: var(--brand-blue);
  }
  .contact { position: absolute; left: 284px; top: 38px; color: var(--ink-white); }
  .contact-name { color: var(--brand-blue); font-weight: 700; font-size: 16px; letter-spacing: 0.5px; }
  .contact-role { font-size: 11.5px; margin-top: 2px; }
  .contact-list { list-style: none; margin-top: 12px; font-size: 11.5px; line-height: 18px; }
  .contact-list li { display: flex; align-items: center; gap: 8px; }
  .contact-list svg { width: 11px; height: 11px; fill: var(--brand-blue); flex: none; }
  .contact-address { margin-top: 10px; font-size: 11.5px; line-height: 16px; padding-left: 19px; }

  /* Back */
  .card-back {
    left: 610px; top: 130px; background: var(--brand-blue);
    display: flex; align-items: center; justify-content: center;
  }
  .back-brand {
    color: var(--ink-white); font-weight: 800; font-size: 52px; letter-spacing: 6px;
  }
</style>
</head>
<body>
<main class="canvas">
  <section class="card card-front">
    <svg class="front-wave" viewBox="0 0 525 300" aria-hidden="true">
      <path d="M0 300 L0 292 C90 238 310 240 525 262 L525 300 Z" fill="#1058b0"/>
      <path d="M6 296 C96 244 312 246 525 268" fill="none" stroke="#0f0f0f" stroke-width="1.5"/>
    </svg>
    <div class="front-brand">TA<br>BRAMLEY</div>
    <div class="front-divider"></div>
    <div class="contact">
      <div class="contact-name">NOLAN PIERCE</div>
      <div class="contact-role">Managing Director</div>
      <ul class="contact-list">
        <li><svg viewBox="0 0 12 12"><path d="M2 1h3l1 3-2 1a7 7 0 0 0 3 3l1-2 3 1v3c0 1-1 1-1 1A10 10 0 0 1 1 2s0-1 1-1z"/></svg>123 456 789</li>
        <li><svg viewBox="0 0 12 12"><rect x="1" y="4" width="10" height="7" rx="1"/><rect x="3" y="1" width="6" height="3"/></svg>123 456 789</li>
        <li><svg viewBox="0 0 12 12"><path d="M1 2h10v8H1z"/><path d="M1 2l5 4 5-4" fill="none" stroke="#161616" stroke-width="1"/></svg>info@yourgmail.com</li>
        <li><svg viewBox="0 0 12 12"><circle cx="6" cy="6" r="5"/></svg>www.yourwebsite.com</li>
      </ul>
      <div class="contact-address">Your address, City<br>State, Zip 1234</div>
    </div>
  </section>

  <section class="card card-back">
    <div class="back-brand">TA BRAMLEY</div>
  </section>
</main>
</body>
</html>
```